Etiketten für ein Kreativbier
Zielgruppe
Wir sind eine kleine Privatbrauerei und unsere Zielgruppe sind Bierliebhaber.
Aufgabenstellung
Wir erweitern unsere Produktpalette um ein Kreativbier, welches nach Schockolade, Banane und Chili schmeckt. Für unsere klassischen Biersorten haben wir auch klassische Etiketten. Für das neue, ausgefallene Bier, suchen wir auch ein dazupassendes, ausgefallenes Etikett. Das Etikett soll die Grundfarbe weiß haben und die Schrift bzw. Grafik soll in schwarz erfolgen. Der Name vom Bier wird 'WIRAPOMELU' sein - Abkürzung für Walnut Raspberry Melon Bier. Unser Logo soll aber in jedem Fall Bestandteil des Etikettes sein. Im Anhang befindet sich eine Etikette von einem Bier aus unserem Sortiment. Die Größe von dem Etikett muss 1:1 übernommen werden. Auch die Linke Seite mit dem Text und dem Druckfeld, muss identisch bleiben, damit es beim Etikettieren keine Probleme gibt.
Das Textfeld soll im Abschnitt Zutaten folgendermaßen angepasst werden: 'Zutaten: Wasser, Gerstenmalz, Weizenmalz, Hopfen, Hefe, Chili'

```html
<!DOCTYPE html>
<html lang="de">
<head>
<meta charset="UTF-8">
<title>WIRA POMELU – Etikett</title>
<link rel="stylesheet" href="https://fonts.googleapis.com/css2?family=Titan+One&display=swap">
<style>
  :root {
    --backdrop: #e7e7e7;
    --label-white: #f3f4f5;
    --ink: #161616;
    --title-ink: #2a2a2a;
    --art-tone: #dcdcdc;
    --art-tone-soft: rgba(220, 220, 220, 0);
  }
  * { box-sizing: border-box; margin: 0; padding: 0; }
  html, body {
    width: 900px;
    height: 1200px;
    overflow: hidden;
    background: var(--backdrop);
  }
  .canvas {
    position: relative;
    width: 900px;
    height: 1200px;
    display: flex;
    align-items: center;
    justify-content: center;
  }
  .label {
    position: relative;
    width: 640px;
    height: 880px;
    background: var(--label-white);
    display: flex;
    flex-direction: column;
    align-items: center;
  }
  .label__band {
    position: absolute;
    left: 0;
    right: 0;
    height: 22px;
    background: var(--ink);
  }
  .label__band--top { top: 0; }
  .label__band--bottom { bottom: 0; }
  .label__rule {
    position: absolute;
    left: 0;
    right: 0;
    height: 8px;
    background: var(--ink);
  }
  .label__rule--top { top: 40px; }
  .label__rule--bottom { bottom: 40px; }
  .brand {
    margin-top: 110px;
    display: flex;
    flex-direction: column;
    align-items: center;
    gap: 12px;
  }
  .brand__dot {
    width: 40px;
    height: 40px;
    border-radius: 50%;
    background: var(--ink);
  }
  .brand__name {
    font-family: "Titan One", sans-serif;
    font-size: 30px;
    letter-spacing: 3px;
    color: var(--ink);
  }
  .artwork {
    margin-top: 22px;
    width: 330px;
    height: 270px;
    background: radial-gradient(ellipse closest-side at 50% 50%, var(--art-tone) 0%, var(--art-tone) 45%, var(--art-tone-soft) 100%);
  }
  .beer-name {
    margin-top: 34px;
    font-family: "Titan One", sans-serif;
    font-size: 100px;
    line-height: 1.08;
    color: var(--title-ink);
    text-align: center;
    letter-spacing: 1px;
  }
</style>
</head>
<body>
  <main class="canvas">
    <section class="label">
      <div class="label__band label__band--top"></div>
      <div class="label__rule label__rule--top"></div>

      <div class="brand">
        <span class="brand__dot"></span>
        <span class="brand__name">HOLZTAL BRÄU</span>
      </div>

      <div class="artwork" role="img" aria-label="Linienzeichnung eines Zweigs mit Blättern und aufgeschnittener Frucht"></div>

      <h1 class="beer-name">WIRA<br>POMELU</h1>

      <div class="label__rule label__rule--bottom"></div>
      <div class="label__band label__band--bottom"></div>
    </section>
  </main>
</body>
</html>
```